Psychiatric Office Needs a Website- 1st Time Ever!

Been in practice since 2003 with no website, but finally ready to dive in. We are Maplecrest Behavioral Healthcare, a mental health outpatient practice based in Fayetteville, Georgia that sees diverse individuals and families from childhood to advanced age for a variety of conditions. We've grown by word of mouth and referral but would now like to have a digital footprint. Be the pioneer of our website and we will be sure to share. We would like to see designs that are modern, animated, fairly colorful, easy to read, and caters to all ages. Also, we would like the design to take the whole page (not be centered) and can be viewed well on phone/tablet. Please see our outline for more information. Our motto/slogan is: Maplecrest Behavioral Healthcare- A step forward in your wellness journey, so the design should try to reflect that.
Updates

Project Deadline Extended
Reason: site in progress

Target Market(s)

Children through elderly

Industry/Entity Type

Medical

Logo Text

Stepping forward in your wellness journey

Number of Pages Required

1 page

Colors

Designer to choose colors to be used in the design.

Requirements
Must have
• Animation or moving pictures.
• Color.
• Concise.
• User friendly
• Diversity in the stock photos

```html
<!DOCTYPE html>
<html lang="en">
<head>
<meta charset="utf-8">
<title>Maplecrest Behavioral Healthcare</title>
<link href="https://fonts.googleapis.com/css2?family=Asap:wght@400;500;600&family=Arimo:wght@400;700&display=swap" rel="stylesheet">
<style>
:root{
  --blue:#2b9ad6;
  --blue-dark:#1f7fb8;
  --green:#7cb342;
  --green-dark:#5f9a2c;
  --ink:#333;
  --muted:#666;
  --white:#fff;
  --line:#d9d9d9;
  --dark:#3a3a3a;
}
*{box-sizing:border-box;margin:0;padding:0}
html,body{width:1200px;height:3455px;overflow:hidden}
body{position:relative;font-family:"Arimo",Arial,sans-serif;color:var(--ink);background:var(--white)}
.abs{position:absolute}
h1,h2,h3,h4{font-family:"Asap",Arial,sans-serif;font-weight:400}

/* header */
.topbar{left:0;top:0;width:1200px;height:50px;background:#fff;font-size:13px;color:#444}
.topbar .item{position:absolute;top:16px;display:flex;align-items:center;gap:8px}
.topbar .sep{position:absolute;top:12px;width:1px;height:24px;background:#bbb}
.navbar{left:0;top:50px;width:1200px;height:70px;background:var(--green)}
.nav{position:absolute;left:355px;top:0;display:flex;height:70px}
.nav a{display:block;color:#fff;text-decoration:none;font-family:"Asap",Arial,sans-serif;font-size:16px;line-height:70px;padding:0 15px}
.nav a.active{background:var(--blue);padding:0 35px;margin-right:12px;margin-top:-18px;line-height:88px;height:88px}
.brand{left:78px;top:10px;width:112px;height:112px;border-radius:50%;background:var(--blue);border:4px solid #fff;box-shadow:0 0 0 2px var(--blue);display:flex;align-items:center;justify-content:center;text-align:center;color:#fff;font-family:"Asap",Arial,sans-serif;font-size:12px;line-height:1.3;padding:14px}

/* hero */
.hero{left:0;top:120px;width:1200px;height:566px;background:linear-gradient(180deg,#8fa36a 0%,#c9c7b4 35%,#6d6a55 70%,#4a3c30 100%)}
.hero-title{left:0;top:300px;width:1200px;text-align:center;color:#fff;font-size:48px;font-family:"Asap",Arial,sans-serif}
.hero-title span{background:rgba(60,60,60,.35);padding:4px 24px}
.hero-tag{left:0;top:362px;width:1200px;text-align:center;color:#fff;font-size:21px;font-style:italic}
.btn{display:block;text-align:center;color:#fff;font-family:"Asap",Arial,sans-serif;text-transform:uppercase}
.hero-btn{left:507px;top:405px;width:186px;height:56px;line-height:56px;background:var(--blue);font-size:19px}

/* vision mission */
.vision{left:0;top:690px;width:600px;height:370px;background:var(--blue)}
.mission{left:600px;top:690px;width:600px;height:370px;background:var(--green)}
.vm-head{position:absolute;top:50px;display:flex;align-items:center;gap:12px;color:#fff;font-size:36px;font-family:"Asap",Arial,sans-serif}
.vm-head:after{content:"";position:absolute;left:0;bottom:-8px;width:178px;height:2px;background:#fff}
.vm-text{position:absolute;top:120px;width:340px;color:#fff;font-size:14px;line-height:25px}
.emblem{left:463px;top:722px;width:274px;height:274px;border-radius:50%;background:var(--blue);border:6px solid #fff;box-shadow:0 0 0 6px var(--blue);display:flex;align-items:center;justify-content:center;text-align:center;color:#fff;font-family:"Asap",Arial,sans-serif;font-size:22px;line-height:1.35;padding:30px}

/* services */
.services{left:0;top:1060px;width:1200px;height:833px;background:linear-gradient(135deg,#4a4a4a,#2f2f2f 55%,#3d3833)}
.sec-title{left:0;width:1200px;text-align:center;color:#fff;font-size:36px}
.sec-title:after{content:"";display:block;width:160px;height:2px;background:#fff;margin:6px auto 0}
.svc{position:absolute;width:230px;color:#fff;font-size:13px;line-height:19px}
.svc h4{color:var(--blue);font-size:16px;margin-bottom:4px}
.svc a{color:#fff;font-weight:700;text-decoration:underline}
.svc-photo{position:absolute;width:128px;height:128px;border-radius:50%;border:5px solid var(--blue);background:linear-gradient(135deg,#e8dcd0,#b98f7a)}

/* conditions */
.conditions{left:0;top:1893px;width:1200px;height:553px;background:linear-gradient(90deg,#2c8fd0,#3fa2be 50%,#6fb04a)}
.cond{position:absolute;top:2043px;width:251px;text-align:center;color:#fff}
.cond .photo{width:251px;height:168px;box-shadow:0 4px 10px rgba(0,0,0,.3)}
.cond h3{font-size:21px;margin:22px 0 16px;line-height:1.1;height:46px;display:flex;align-items:flex-start;justify-content:center}
.cond p{font-size:13px;line-height:19px;padding:0 8px}
.arrow{position:absolute;top:2106px;width:30px;height:30px;background:#fff;color:var(--blue-dark);display:flex;align-items:center;justify-content:center}
.dots{left:572px;top:2410px;display:flex;gap:4px}
.dots i{display:block;width:14px;height:14px;border:2px solid #fff}
.dots i.on{background:#fff}

/* faq / news */
.faq-news{left:0;top:2446px;width:1200px;height:428px;background:#fff}
.divider{left:612px;top:2446px;width:8px;height:428px;background:#eee}
.col-title{font-size:36px;color:var(--blue)}
.faq{left:78px;top:2555px;width:520px}
.faq .q{border:1px solid var(--line);height:44px;display:flex;align-items:center;gap:14px;padding:0 16px;color:var(--blue-dark);font-size:18px;font-family:"Asap",Arial,sans-serif}
.faq .q .sign{color:var(--green);font-size:26px;font-weight:700;width:18px}
.faq .a{border:1px solid var(--line);border-top:none;padding:12px 16px;font-size:11px;line-height:17px;color:#555}
.news{position:absolute;left:668px;width:460px;display:flex;gap:22px}
.news .thumb{width:116px;height:112px;flex:none;background:linear-gradient(135deg,#d7c7b6,#7d8c9e)}
.news h4{color:var(--blue);font-size:18px;margin:6px 0 6px}
.news .date{color:var(--green);font-size:11px;margin-bottom:6px}
.news p{font-size:13px;line-height:19px;color:#555}
.news .more{color:var(--blue);font-size:12px;margin-top:10px}

/* cta */
.cta{left:0;top:2874px;width:1200px;height:106px;background:var(--blue)}
.cta p{position:absolute;left:80px;top:28px;width:780px;color:#fff;font-size:14px;line-height:26px}
.cta-btn{left:896px;top:2900px;width:228px;height:55px;line-height:55px;background:var(--green);font-size:18px}

/* footer */
.footer{left:0;top:2980px;width:1200px;height:405px;background:linear-gradient(135deg,#5d7a3a,#3f5f2b 40%,#6f8a45 80%,#4a6a30)}
.footer:before{content:"";position:absolute;inset:0;background:rgba(40,60,30,.35)}
.ft-title{position:absolute;top:3047px;color:#fff;font-size:19px;text-transform:uppercase}
.field{position:absolute;left:80px;width:447px;height:40px;background:#fff;color:#666;font-size:13px;padding:11px 10px}
.submit{left:80px;top:3325px;width:185px;height:51px;line-height:51px;background:var(--blue);font-size:17px}
.links{left:569px;top:3083px;list-style:none;color:#fff;font-size:14px;line-height:29px}
.links li:before{content:"";display:inline-block;width:7px;height:7px;border-radius:50%;background:var(--blue);margin-right:12px;vertical-align:middle}
.find{position:absolute;left:873px;color:#fff;font-size:13px;line-height:20px;display:flex;gap:16px}
.find svg{flex:none}
.social{left:873px;top:3307px;display:flex;gap:18px}
.social i{display:block;width:44px;height:44px;border-radius:50%;background:var(--blue)}
.copy{left:0;top:3385px;width:1200px;height:70px;background:#fff;text-align:center;line-height:70px;font-size:13px;color:#333;border-top:1px solid #ddd}
</style>
</head>
<body>

<!-- header -->
<div class="abs topbar">
  <div class="item" style="left:505px">
    <svg width="16" height="16" viewBox="0 0 16 16"><circle cx="8" cy="8" r="7" fill="none" stroke="#555" stroke-width="1.6"/><path d="M8 4v4l3 2" stroke="#555" stroke-width="1.6" fill="none"/></svg>
    Monday - Friday : 10.00 A.M to 8.00 P.M
  </div>
  <span class="sep" style="left:808px"></span>
  <div class="item" style="left:825px">
    <svg width="16" height="16" viewBox="0 0 16 16"><rect x="1" y="1" width="14" height="14" rx="3" fill="#555"/><path d="M5 4l2 2-1 1c1 2 2 3 3 3l1-1 2 2-1 1c-3 0-7-4-7-7z" fill="#fff"/></svg>
    +1-555-014-2300
  </div>
  <span class="sep" style="left:962px"></span>
  <div class="item" style="left:980px">LOGIN</div>
  <div class="item" style="left:1036px">
    <svg width="14" height="16" viewBox="0 0 14 16"><circle cx="7" cy="4" r="3.5" fill="var(--green)"/><path d="M0 16c0-5 3-7 7-7s7 2 7 7z" fill="var(--green)"/></svg>
    Patient
  </div>
</div>
<div class="abs navbar">
  <nav class="nav">
    <a class="active" href="#">Home</a>
    <a href="#">About Us</a>
    <a href="#">Services</a>
    <a href="#">Conditions We Treat</a>
    <a href="#">New Patients</a>
    <a href="#">Contact Us</a>
  </nav>
</div>
<div class="abs brand">Maplecrest Behavioral Healthcare</div>

<!-- hero -->
<div class="abs hero" role="img" aria-label="Photo of a person sitting on a park bench with an arm around a friend, sunny trees behind"></div>
<h1 class="abs hero-title"><span>Maplecrest Behavioral Healthcare</span></h1>
<p class="abs hero-tag">A step forward in your wellness journey</p>
<a class="abs btn hero-btn" href="#">Contact Us</a>

<!-- vision / mission -->
<section class="abs vision">
  <h2 class="vm-head" style="left:78px">
    <svg width="34" height="34" viewBox="0 0 34 34"><path d="M6 10l18-6 3 8-18 6z" fill="#fff"/><path d="M15 17l-6 15M17 16l6 16" stroke="#fff" stroke-width="2.5"/></svg>
    VISION
  </h2>
  <p class="vm-text" style="left:78px">Lorem Ipsum is simply dummy text of the printing and typesetting industry. Lorem Ipsum has been the industry's standard dummy text ever since the 1500s, when an unknown printer took a galley of type and scrambled it to make a type specimen book. It has survived not only five centuries, but also the leap into electronic typesetting, remaining essentially unchanged.</p>
</section>
<section class="abs mission">
  <h2 class="vm-head" style="left:170px">
    <svg width="36" height="36" viewBox="0 0 36 36"><circle cx="17" cy="19" r="14" fill="none" stroke="#fff" stroke-width="3"/><circle cx="17" cy="19" r="7" fill="none" stroke="#fff" stroke-width="3"/><path d="M17 19L33 3" stroke="#fff" stroke-width="3"/></svg>
    MISSION
  </h2>
  <p class="vm-text" style="left:172px">Lorem Ipsum is simply dummy text of the printing and typesetting industry. Lorem Ipsum has been the industry's standard dummy text ever since the 1500s, when an unknown printer took a galley of type and scrambled it to make a type specimen book. It has survived not only five centuries, but also the leap into electronic typesetting, remaining essentially unchanged.</p>
</section>
<div class="abs emblem">Maplecrest Behavioral Healthcare</div>

<!-- services -->
<section class="abs services" role="img" aria-label="Dimmed background photo of a counselling session"></section>
<h2 class="abs sec-title" style="top:1105px">SERVICES</h2>
<svg class="abs" style="left:0;top:1060px" width="1200" height="833">
  <g stroke="#7cb342" stroke-width="2">
    <line x1="599" y1="391" x2="500" y2="207"/><line x1="599" y1="391" x2="686" y2="195"/>
    <line x1="599" y1="391" x2="398" y2="345"/><line x1="599" y1="391" x2="799" y2="326"/>
    <line x1="599" y1="391" x2="446" y2="530"/><line x1="599" y1="391" x2="765" y2="518"/>
    <line x1="599" y1="391" x2="608" y2="596"/>
  </g>
  <circle cx="599" cy="391" r="104" fill="#d9d9d9" stroke="#ececec" stroke-width="6"/>
  <circle cx="599" cy="391" r="52" fill="none" stroke="var(--blue)" stroke-width="8"/>
  <g fill="#fff">
    <circle cx="497" cy="320" r="5"/><circle cx="701" cy="320" r="5"/><circle cx="497" cy="462" r="5"/><circle cx="701" cy="462" r="5"/><circle cx="599" cy="497" r="5"/>
  </g>
</svg>
<div class="svc-photo" role="img" aria-label="Photo of a diagnostic evaluation meeting" style="left:436px;top:1203px"></div>
<div class="svc-photo" role="img" aria-label="Photo of a parent and child reading together" style="left:622px;top:1191px"></div>
<div class="svc-photo" role="img" aria-label="Photo of a doctor talking with a patient" style="left:334px;top:1341px"></div>
<div class="svc-photo" role="img" aria-label="Photo of a mother and young child" style="left:735px;top:1322px"></div>
<div class="svc-photo" role="img" aria-label="Photo of a consultation across a desk" style="left:382px;top:1526px"></div>
<div class="svc-photo" role="img" aria-label="Photo of a troubled young woman" style="left:701px;top:1514px"></div>
<div class="svc-photo" role="img" aria-label="Photo of a child at a table" style="left:544px;top:1592px"></div>

<div class="svc" style="left:139px;top:1216px"><h4>Diagnostic evaluation and treatment</h4><p style="padding-left:0">Lorem Ipsum is simply dummy text of the printing and text typesetting industry.<a>READ MORE</a></p></div>
<div class="svc" style="left:770px;top:1198px"><h4>Disability and work-related reports</h4><p>Lorem Ipsum is simply dummy text of the printing and text typesetting industry.<a>READ MORE</a></p></div>
<div class="svc" style="left:80px;top:1383px"><h4>Psychopharmacology</h4><p>Lorem Ipsum is simply dummy text of the printing and text typesetting industry.<a>READ MORE</a></p></div>
<div class="svc" style="left:887px;top:1357px"><h4>Early childhood Assessments</h4><p>Lorem Ipsum is simply dummy text of the printing and text typesetting industry.<a>READ MORE</a></p></div>
<div class="svc" style="left:100px;top:1574px;width:270px"><h4>Bariatric pre-surgical consultation</h4><p>Lorem Ipsum is simply dummy text of the printing and text typesetting industry.<a>READ MORE</a></p></div>
<div class="svc" style="left:863px;top:1543px"><h4>Substance abuse assessments</h4><p>Lorem Ipsum is simply dummy text of the printing and text typesetting industry.<a>READ MORE</a></p></div>
<div class="svc" style="left:500px;top:1748px;width:220px"><h4>Developmental disabilities</h4><p>Lorem Ipsum is simply dummy text of the printing and text typesetting industry.<a>READ MORE</a></p></div>

<!-- conditions -->
<section class="abs conditions"></section>
<h2 class="abs sec-title" style="top:1952px">CONDITIOND WE TREAT</h2>
<div class="cond" style="left:78px"><div class="photo" role="img" aria-label="Photo of a woman holding her head in distress" style="background:linear-gradient(135deg,#222,#8a6d5c)"></div><h3>Mood Disorders</h3><p>Lorem Ipsum is simply dummy text of the printing and typesetting industry. Lorem Ipsum has been the industry's standard dummy text ever since.</p></div>
<div class="cond" style="left:343px"><div class="photo" role="img" aria-label="Photo of a nurse comforting a patient" style="background:linear-gradient(135deg,#9fc7d8,#b56a62)"></div><h3>Anxiety Disorders</h3><p>Lorem Ipsum is simply dummy text of the printing and typesetting industry. Lorem Ipsum has been the industry's standard dummy text ever since.</p></div>
<div class="cond" style="left:608px"><div class="photo" role="img" aria-label="Photo of a therapist talking with an older man" style="background:linear-gradient(135deg,#8b6b4d,#c9c0b6)"></div><h3>Psychotic Disorders</h3><p>Lorem Ipsum is simply dummy text of the printing and typesetting industry. Lorem Ipsum has been the industry's standard dummy text ever since.</p></div>
<div class="cond" style="left:873px"><div class="photo" role="img" aria-label="Photo of a mother hugging her child" style="background:linear-gradient(135deg,#5f7a3c,#a5764f)"></div><h3>Common Disorders<br>of Childhood</h3><p>Lorem Ipsum is simply dummy text of the printing and typesetting industry. Lorem Ipsum has been the industry's standard dummy text ever since.</p></div>
<div class="arrow" style="left:32px"><svg width="12" height="14" viewBox="0 0 12 14"><path d="M9 1L3 7l6 6" stroke="currentColor" stroke-width="2.5" fill="none"/></svg></div>
<div class="arrow" style="left:1141px"><svg width="12" height="14" viewBox="0 0 12 14"><path d="M3 1l6 6-6 6" stroke="currentColor" stroke-width="2.5" fill="none"/></svg></div>
<div class="abs dots"><i></i><i class="on"></i><i></i></div>

<!-- faq and news -->
<section class="abs faq-news"></section>
<div class="abs divider"></div>
<h2 class="abs col-title" style="left:78px;top:2490px">FAQ</h2>
<h2 class="abs col-title" style="left:668px;top:2490px">LATEST NEWS</h2>
<div class="abs faq">
  <div class="q"><span class="sign">&minus;</span>What do I need to bring with me to my first visit?</div>
  <div class="a">Lorem Ipsum is simply dummy text of the printing and typesetting industry. Lorem Ipsum has been the industry's standard dummy text ever since the 1500s. It has survived not only five centuries, but also the leap into electronic typesetting, remaining essentially unchanged.</div>
  <div class="q"><span class="sign">+</span>How long do I have to wait to be seen?</div>
  <div class="q"><span class="sign">+</span>Why is my child not doing well in school?</div>
  <div class="q"><span class="sign">+</span>What typs of insurance do you accept?</div>
</div>
<div class="news" style="top:2555px">
  <div class="thumb" role="img" aria-label="Photo of a young woman with her hands on her head"></div>
  <div><h4>Lorem Ipsum is simply dummy text</h4><div class="date">&#9635; 10 JULY 2016</div><p>Lorem Ipsum is simply dummy text of the printing and typesetting industry......</p><div class="more">READ MORE &nbsp;&nbsp;&raquo;</div></div>
</div>
<div class="abs" style="left:800px;top:2686px;width:280px;height:1px;background:var(--line)"></div>
<div class="news" style="top:2713px">
  <div class="thumb" role="img" aria-label="Photo of a family reading together"></div>
  <div><h4>Lorem Ipsum is simply dummy text</h4><div class="date">&#9635; 10 JULY 2016</div><p>Lorem Ipsum is simply dummy text of the printing and typesetting industry......</p><div class="more">READ MORE &nbsp;&nbsp;&raquo;</div></div>
</div>

<!-- call to action -->
<section class="abs cta"><p>Lorem Ipsum is simply dummy text of the printing and typesetting industry. Lorem Ipsum has been the industry's standard dummy text ever since the 1500s, when an unknown printer took a galley of type and scrambled.</p></section>
<a class="abs btn cta-btn" href="#">New Patient Form</a>

<!-- footer -->
<footer class="abs footer" role="img" aria-label="Soft green background photo of people outdoors"></footer>
<h3 class="ft-title" style="left:80px">Quick Inquiry</h3>
<h3 class="ft-title" style="left:569px">Our Services</h3>
<h3 class="ft-title" style="left:873px">Find Us</h3>
<div class="field" style="top:3086px">Name*</div>
<div class="field" style="top:3132px">Email*</div>
<div class="field" style="top:3178px">Services*</div>
<div class="field" style="top:3224px;height:92px">Message*</div>
<a class="abs btn submit" href="#">Submit</a>
<ul class="abs links">
  <li>Home</li><li>About Us</li><li>Services</li><li>Conditions We Treat</li><li>New Patients</li><li>Contact Us</li>
</ul>
<div class="find" style="top:3080px">
  <svg width="18" height="24" viewBox="0 0 18 24"><path d="M9 0a9 9 0 0 1 9 9c0 6-9 15-9 15S0 15 0 9a9 9 0 0 1 9-9z" fill="var(--blue)"/><circle cx="9" cy="9" r="3.5" fill="#fff"/></svg>
  <div>Maplecrest Behavioral Healthcare<br>Lorem Ipsum is simply dummy<br>text printing and typesetting</div>
</div>
<div class="find" style="top:3170px">
  <svg width="20" height="20" viewBox="0 0 20 20"><path d="M4 1l4 4-2 3c1 3 3 5 6 6l3-2 4 4-3 3C8 19 1 12 1 4z" fill="var(--blue)"/></svg>
  <div>+1-555-014-2300</div>
</div>
<div class="find" style="top:3216px">
  <svg width="20" height="20" viewBox="0 0 20 20"><rect x="2" y="1" width="16" height="18" rx="2" fill="var(--blue)"/><rect x="5" y="4" width="10" height="5" fill="#fff"/></svg>
  <div>+1-555-014-2300</div>
</div>
<div class="find" style="top:3260px">
  <svg width="20" height="16" viewBox="0 0 20 16"><rect width="20" height="16" rx="2" fill="var(--blue)"/><path d="M1 2l9 7 9-7" stroke="#fff" stroke-width="1.6" fill="none"/></svg>
  <div>info@maplecresthealth.example</div>
</div>
<div class="abs social"><i></i><i></i><i></i></div>
<div class="abs copy">&copy; MAPLECREST BEHAVIORAL HEALTHCARE- 2017. All Rights Reserved</div>

</body>
</html>
```